Boutique custom software development company needs new business card

Our nearly 20 year old custom software development company would like to better include the fact that we are now providing Bitcoin services. These new services are B2B include education (how to acquire and securely hold Bitcoin) and integrating Bitcoin payments into existing ecommerce sites or other existing systems. Please keep the card clean and simple. Attached is our current design and some other files. vextorial.com

Target Market(s)

businesses owners interested in long term relationship

Industry/Entity Type

Custom software development and Bitcoin

Contact Information for Business Card

Dale Parker, dale@vextorial.com, vextorial.com, (888) 555-VXTRL

Font styles to use
Other font styles liked:
• monospace

Requirements
Must have
• double-sided
Nice to have
• clean and simple
Should not have
• physical address

```html
<!DOCTYPE html>
<html lang="en">
<head>
<meta charset="utf-8">
<title>Vextorial Business Card</title>
<link href="https://fonts.googleapis.com/css2?family=Roboto+Mono:wght@400;500;700&family=Lato:wght@400&display=swap" rel="stylesheet">
<style>
  :root {
    --backdrop: #141414;
    --card-navy: #071432;
    --brand-blue: #3f74bc;
    --brand-orange: #ef7b22;
    --text-white: #f2f4f8;
  }
  * { margin: 0; padding: 0; box-sizing: border-box; }
  html, body {
    width: 1200px; height: 848px; overflow: hidden;
    background: var(--backdrop);
  }
  .canvas { position: relative; width: 1200px; height: 848px; }
  .card {
    position: absolute;
    left: 281px; width: 615px; height: 333px;
    background: var(--card-navy);
    border-radius: 18px;
  }
  .card--front { top: 68px; }
  .card--back { top: 445px; }

  .front-mark {
    position: absolute; left: 0; right: 0; top: 140px;
    display: flex; align-items: center; justify-content: center; gap: 14px;
  }
  .front-mark__square {
    width: 44px; height: 44px; background: var(--brand-orange);
  }
  .front-mark__name {
    font-family: "Roboto Mono", monospace; font-weight: 700;
    font-size: 40px; letter-spacing: 1px; color: var(--brand-blue);
  }

  .back-brand {
    position: absolute; right: 30px; top: 28px;
    text-align: center;
  }
  .back-brand__name {
    font-family: "Roboto Mono", monospace; font-weight: 700;
    font-size: 42px; line-height: 1; letter-spacing: 1px;
    color: var(--brand-blue);
  }
  .back-brand__tagline {
    margin-top: 10px;
    font-family: "Lato", sans-serif; font-size: 15px; letter-spacing: -0.4px;
    color: var(--brand-blue);
  }

  .holder-name {
    position: absolute; left: 30px; top: 196px;
    font-family: "Roboto Mono", monospace; font-weight: 500;
    font-size: 24px; letter-spacing: 0.5px; color: var(--brand-blue);
  }
  .contact-list {
    position: absolute; left: 30px; top: 250px;
    list-style: none;
    font-family: "Roboto Mono", monospace; font-size: 14px;
    color: var(--text-white);
  }
  .contact-list li {
    display: flex; align-items: center; gap: 7px; height: 18.7px;
  }
  .contact-list svg { width: 12px; height: 12px; fill: var(--brand-blue); flex: none; }
</style>
</head>
<body>
<main class="canvas">
  <section class="card card--front" aria-label="Card front">
    <div class="front-mark">
      <span class="front-mark__square"></span>
      <span class="front-mark__name">VEXTORIAL</span>
    </div>
  </section>

  <section class="card card--back" aria-label="Card back">
    <div class="back-brand">
      <div class="back-brand__name">VEXTORIAL</div>
      <div class="back-brand__tagline">developer of custom applications</div>
    </div>

    <h1 class="holder-name">Dale Parker</h1>

    <ul class="contact-list">
      <li>
        <svg viewBox="0 0 24 24" aria-hidden="true"><path d="M6.6 10.8a15.1 15.1 0 0 0 6.6 6.6l2.2-2.2c.3-.3.7-.4 1-.2 1.1.4 2.3.6 3.6.6.6 0 1 .4 1 1V20c0 .6-.4 1-1 1A17 17 0 0 1 3 4c0-.6.4-1 1-1h3.5c.6 0 1 .4 1 1 0 1.3.2 2.5.6 3.6.1.3 0 .7-.2 1z"/></svg>
        (888) 555-VXTRL
      </li>
      <li>
        <svg viewBox="0 0 24 24" aria-hidden="true"><path d="M2 5h20v14H2z M2 5l10 8 10-8" /></svg>
        dale@vextorial.com
      </li>
      <li>
        <svg viewBox="0 0 24 24" aria-hidden="true"><path d="M12 2a10 10 0 1 0 0 20 10 10 0 0 0 0-20zm6.9 6h-3a15.7 15.7 0 0 0-1.4-3.6A8 8 0 0 1 18.9 8zM12 4c.8 1.2 1.5 2.5 1.9 4h-3.8c.4-1.5 1.1-2.8 1.9-4zM4.3 14a8.2 8.2 0 0 1 0-4h3.4a16.5 16.5 0 0 0 0 4zm.8 2h3a15.7 15.7 0 0 0 1.4 3.6A8 8 0 0 1 5.1 16zm3-8h-3a8 8 0 0 1 4.4-3.6C8.9 5.5 8.4 6.7 8.1 8zM12 20c-.8-1.2-1.5-2.5-1.9-4h3.8c-.4 1.5-1.1 2.8-1.9 4zm2.3-6H9.7a14.7 14.7 0 0 1 0-4h4.6a14.7 14.7 0 0 1 0 4zm.3 5.6c.6-1.1 1.1-2.3 1.4-3.6h3a8 8 0 0 1-4.4 3.6zm1.7-5.6a16.5 16.5 0 0 0 0-4h3.4a8.2 8.2 0 0 1 0 4z"/></svg>
        vextorial.com
      </li>
    </ul>
  </section>
</main>
</body>
</html>
```